Professional looking Roller Blind Discount Card that portrays quality at a value for money price!

We need a double sided business card designed as a discount card. Size 90mm wide x 55mm high.We would like it to look professional and portray quality at a value for money price point.I have uploaded a word document with a basic layout with the information we want included on each side of the card. Please put your own thought into the layout.

Contact Information for Business Card

As per word document attached.

```html
<!DOCTYPE html>
<html lang="en">
<head>
<meta charset="utf-8">
<title>Roller Blinds Discount Card – Front and Back</title>
<link rel="stylesheet" href="https://fonts.googleapis.com/css2?family=League+Spartan:wght@700;800;900&family=Quicksand:wght@500;600;700&family=Fira+Sans+Condensed:wght@800&family=Montserrat:wght@800&display=swap">
<style>
  :root {
    --page-bg: #ffffff;
    --card-bg: #abdcee;
    --frame-blue: #0f5488;
    --headline-ink: #1a0833;
    --headline-shadow: #145b93;
    --subhead-blue: #0f4f80;
    --pill-blue: #2e8fd4;
    --white: #ffffff;
    --black-ink: #1b1b1b;
    --phone-blue: #13618f;
    --title-blue: #0a3a80;
    --title-shadow: #061c3c;
    --fabric-box: #1a5b97;
    --fabric-box-light: #2f78b8;
    --brand-blue: #2e8fd4;
    --seal-red: #ff2a1a;
    --seal-orange: #ff5a14;
  }
  * { margin: 0; padding: 0; box-sizing: border-box; }
  html, body { width: 1200px; height: 1200px; overflow: hidden; background: var(--page-bg); }
  .sheet { position: relative; width: 1200px; height: 1200px; }

  .card {
    position: absolute;
    left: 152px;
    width: 890px;
    height: 545px;
    background: var(--card-bg);
    box-shadow: 0 3px 8px rgba(0,0,0,0.18);
    overflow: hidden;
  }
  .card--front { top: 42px; }
  .card--back { top: 612px; }

  .rule { position: absolute; background: var(--frame-blue); }

  /* Front */
  .offer-headline {
    position: absolute; left: 0; right: 0; top: 45px;
    text-align: center;
    font-family: "League Spartan", sans-serif; font-weight: 900;
    font-size: 126px; line-height: 1; letter-spacing: 1px;
    color: var(--headline-ink);
    text-shadow: -5px 5px 0 var(--headline-shadow);
  }
  .offer-subhead {
    position: absolute; left: 0; right: 0; top: 175px;
    text-align: center;
    font-family: "Fira Sans Condensed", sans-serif; font-weight: 800;
    font-size: 46px; line-height: 1; letter-spacing: 1.5px;
    color: var(--subhead-blue);
  }
  .fabric-types {
    position: absolute; left: 127px; top: 242px; width: 645px; height: 59px;
    border-radius: 22px; background: var(--pill-blue);
    color: var(--white);
    font-family: "Quicksand", sans-serif; font-weight: 500;
    font-size: 38px; line-height: 59px; text-align: center;
  }
  .seal {
    position: absolute; top: 329px; width: 153px; height: 128px;
    border-radius: 50%;
    background: radial-gradient(circle at 50% 45%, var(--seal-orange) 0%, var(--seal-red) 80%);
  }
  .seal--measure { left: 103px; }
  .seal--guarantee { left: 374px; }
  .seal--family { left: 635px; }

  .call-line {
    position: absolute;
    font-family: "League Spartan", sans-serif; font-weight: 700;
    font-size: 44px; line-height: 1; letter-spacing: 2px;
    color: var(--black-ink); white-space: nowrap;
  }
  .call-line .phone { color: var(--phone-blue); letter-spacing: 1.5px; }
  .card--front .call-line { left: 154px; top: 487px; }

  /* Back */
  .back-title {
    position: absolute; left: 0; right: 0; top: 41px;
    text-align: center;
    font-family: "League Spartan", sans-serif; font-weight: 800;
    font-size: 78px; line-height: 1; letter-spacing: 1px;
    color: var(--title-blue);
    text-shadow: -3px 3px 0 var(--title-shadow);
  }
  .title-divider { position: absolute; left: 186px; top: 125px; width: 518px; height: 1.5px; background: var(--black-ink); }
  .service-line {
    position: absolute; left: 0; right: 0; top: 144px;
    text-align: center;
    font-family: "Quicksand", sans-serif; font-weight: 600;
    font-size: 37px; line-height: 1; letter-spacing: 1px;
    color: var(--black-ink);
  }
  .install-photo {
    position: absolute; left: 117px; top: 205px; width: 326px; height: 196px;
    background: linear-gradient(100deg, #6b5a50 0%, #8a7a6c 12%, #5f7f4c 30%, #86a46a 55%, #a8b89a 75%, #c9c4b8 100%);
  }
  .fabric-panel {
    position: absolute; left: 523px; top: 203px; width: 236px; height: 196px;
    background: radial-gradient(circle at 40% 30%, var(--fabric-box-light) 0%, var(--fabric-box) 70%);
    display: flex; align-items: center; justify-content: center;
    color: var(--white); text-align: center;
    font-family: "Montserrat", sans-serif; font-weight: 800;
    font-size: 23px; line-height: 1.4; letter-spacing: -0.5px;
  }
  .card--back .call-line { left: 38px; top: 461px; }
  .brand-name {
    position: absolute; left: 693px; top: 486px;
    font-family: "Quicksand", sans-serif; font-weight: 600;
    font-size: 19px; letter-spacing: 0.5px;
    color: var(--brand-blue); white-space: nowrap;
  }
</style>
</head>
<body>
<main class="sheet">

  <section class="card card--front" aria-label="Card front">
    <div class="rule" style="left:19px; top:18px; width:856px; height:4px;"></div>
    <div class="rule" style="left:19px; top:18px; width:4px; height:495px;"></div>
    <div class="rule" style="left:871px; top:18px; width:4px; height:495px;"></div>
    <div class="rule" style="left:19px; top:509px; width:121px; height:4px;"></div>
    <div class="rule" style="left:750px; top:509px; width:125px; height:4px;"></div>

    <h1 class="offer-headline">25% OFF</h1>
    <h2 class="offer-subhead">Quality Custom Made Roller Blinds</h2>
    <p class="fabric-types">Blockout - Screen - Light Filtering</p>

    <div class="seal seal--measure" role="img" aria-label="Best price seal: free in home measure and quote"></div>
    <div class="seal seal--guarantee" role="img" aria-label="Best price guarantee seal"></div>
    <div class="seal seal--family" role="img" aria-label="Best price seal: family owned and operated"></div>

    <p class="call-line">CALL TODAY : <span class="phone">0400 123 456</span></p>
  </section>

  <section class="card card--back" aria-label="Card back">
    <div class="rule" style="left:593px; top:17px; width:280px; height:4px;"></div>
    <div class="rule" style="left:865px; top:17px; width:4px; height:203px;"></div>
    <div class="rule" style="left:19px; top:320px; width:4px; height:205px;"></div>
    <div class="rule" style="left:19px; top:521px; width:277px; height:4px;"></div>

    <h1 class="back-title">ROLLER BLINDS</h1>
    <div class="title-divider"></div>
    <p class="service-line">FREE in Home Measure &amp; Quote</p>

    <div class="install-photo" role="img" aria-label="Photo of white roller blinds installed above a row of windows looking onto a garden"></div>
    <div class="fabric-panel"><p>HUGE SELECTION<br>OF FABRICS</p></div>

    <p class="call-line">CALL TODAY : <span class="phone">0400 123 456</span></p>
    <p class="brand-name">B&amp;K INTERIORS</p>
  </section>

</main>
</body>
</html>
```